Orbit Voltix VR is the name of our project, We are a Virtual Reality Theme park

We need a web page and logo that is sharp and exciting, and futuristic that people would want to have on a tee shirt.. We like teal -black- silver colour. Customers will be able to book on line- we will have Free Roam VR experiences , Trundla(treadmills), Stand alone VR stations and VR Simulator rides.

Orbit Voltix VR

```html
<!DOCTYPE html>
<html lang="en">
<head>
<meta charset="utf-8">
<title>Orbit Voltix VR – Virtual Reality Theme Park</title>
<link rel="stylesheet" href="https://fonts.googleapis.com/css2?family=Saira+Semi+Condensed:wght@500;600;700&family=Roboto:wght@400;500&display=swap">
<style>
:root{
  --teal:#1fc6c0;
  --teal-deep:#0f8f8c;
  --ink:#1b1d20;
  --bg:#121416;
  --bg-2:#1a1d20;
  --silver:#c8cdd2;
  --white:#ffffff;
  --muted:#b9bec3;
}
*{box-sizing:border-box;margin:0;padding:0}
html,body{width:1200px;height:4072px;overflow:hidden;background:var(--bg)}
body{font-family:"Roboto",sans-serif;color:var(--white)}
.page{position:relative;width:1200px;height:4072px;overflow:hidden;background:var(--bg)}
.abs{position:absolute}
.heading{font-family:"Saira Semi Condensed",sans-serif;font-weight:700}

/* hero */
.hero-photo{left:0;top:0;width:1200px;height:680px;
  background:
    radial-gradient(ellipse 260px 300px at 930px 360px,rgba(238,196,40,.85),rgba(238,196,40,0) 70%),
    radial-gradient(ellipse 380px 340px at 950px 380px,rgba(52,60,74,.9),rgba(52,60,74,0) 75%),
    radial-gradient(ellipse 300px 420px at 90px 300px,rgba(214,128,48,.75),rgba(214,128,48,0) 70%),
    radial-gradient(ellipse 360px 200px at 560px 560px,rgba(184,110,52,.6),rgba(184,110,52,0) 70%),
    linear-gradient(180deg,#f4f5f6 0%,#e8eaec 45%,#c9ccd0 78%,#33373b 100%)}
.brand{left:88px;top:42px;font-family:"Saira Semi Condensed",sans-serif;font-weight:700;font-size:34px;color:var(--ink);letter-spacing:.5px}
.nav{left:468px;top:52px;display:flex;gap:38px;list-style:none;font-size:17px;font-weight:500;color:var(--ink)}
.btn-book{left:1000px;top:40px;width:126px;height:46px;border-radius:23px;background:var(--teal);color:var(--white);
  font-size:16px;font-weight:500;display:flex;align-items:center;justify-content:center}
.hero-title{left:88px;top:228px;font-size:78px;color:var(--ink);line-height:1}
.hero-sub{left:88px;top:322px;font-size:54px;color:var(--teal);font-weight:600;line-height:1}

.curve{left:0;width:1200px;height:140px}

/* about */
.about-bg{left:0;top:660px;width:1200px;height:680px;
  background:radial-gradient(ellipse 420px 380px at 1000px 900px,#3a3f45,rgba(58,63,69,0) 70%),linear-gradient(90deg,#1b1e21,#101214)}
.about-photo{left:0;top:680px;width:640px;height:640px;
  background:
    radial-gradient(ellipse 170px 130px at 230px 210px,rgba(230,232,236,.75),rgba(230,232,236,0) 70%),
    radial-gradient(ellipse 220px 160px at 420px 450px,rgba(40,70,170,.55),rgba(40,70,170,0) 70%),
    radial-gradient(ellipse 260px 300px at 240px 440px,#3a3e44,rgba(58,62,68,0) 75%),
    linear-gradient(90deg,#2c3035 0%,#1d2023 70%,rgba(16,18,20,0) 100%)}
.about-title{left:612px;top:816px;font-size:46px}
.about-lead{left:612px;top:880px;font-size:26px;color:var(--white)}
.about-text{left:612px;top:928px;width:530px;font-size:15px;line-height:1.5;color:var(--muted)}
.btn-outline{border:2px solid var(--teal);border-radius:22px;color:var(--white);font-size:16px;
  display:flex;align-items:center;justify-content:center}
.about-btn{left:612px;top:1122px;width:132px;height:42px}

/* attractions */
.rides-bg{left:0;top:1330px;width:1200px;height:680px;background:linear-gradient(180deg,#141619,#1b1e21)}
.section-title{left:0;width:1200px;text-align:center;font-size:46px}
.ride-card{top:1512px;width:330px;height:376px;border:2px solid #d9dde0;overflow:hidden}
.ride-card .media{position:absolute;inset:0}
.ride-label{position:absolute;left:32px;right:32px;bottom:16px;height:48px;background:var(--teal-deep);
  color:var(--white);font-size:18px;display:flex;align-items:center;justify-content:center}
.dots{left:0;top:1956px;width:1200px;display:flex;justify-content:center;gap:14px}
.dot{width:10px;height:10px;border-radius:50%;background:#555b60}
.dot.on{background:var(--teal)}

/* offer */
.offer-bg{left:0;top:2010px;width:1200px;height:620px;
  background:
    radial-gradient(ellipse 420px 160px at 1050px 2300px,rgba(220,60,110,.35),rgba(220,60,110,0) 70%),
    linear-gradient(90deg,#121416 0%,#1b1e22 55%,#241f29 100%)}
.offer-photo{left:520px;top:2060px;width:680px;height:570px;
  background:
    radial-gradient(ellipse 150px 70px at 350px 120px,rgba(235,236,240,.8),rgba(235,236,240,0) 75%),
    radial-gradient(ellipse 160px 200px at 340px 230px,rgba(206,150,120,.7),rgba(206,150,120,0) 70%),
    radial-gradient(ellipse 260px 190px at 370px 470px,#0d0e10,rgba(13,14,16,0) 75%),
    radial-gradient(ellipse 300px 260px at 360px 300px,#3c3f46,rgba(40,30,45,0) 75%)}
.offer-title{left:100px;top:2172px;font-size:64px;line-height:1}
.offer-free{left:100px;top:2250px;font-size:64px;line-height:1;color:var(--teal)}
.offer-text{left:100px;top:2332px;width:440px;font-size:19px;line-height:1.5;font-weight:500}
.offer-btn{left:100px;top:2472px;width:166px;height:44px}

/* blog */
.blog-bg{left:0;top:2630px;width:1200px;height:590px;background:linear-gradient(180deg,#1a1c1f,#121416)}
.blog-card{top:2828px;height:282px;border:5px solid var(--teal);overflow:hidden}
.blog-card .media{position:absolute;inset:0}
.blog-body{position:absolute;inset:0;display:flex;flex-direction:column;align-items:center;justify-content:center;
  text-align:center;padding:0 40px;background:rgba(10,12,14,.35)}
.blog-title{font-size:23px;line-height:1.35;font-weight:500}
.blog-meta{margin-top:12px;font-size:15px;display:flex;gap:18px;justify-content:center}
.blog-meta svg{vertical-align:-2px;margin-right:5px}
.blog-comments{margin-top:8px;font-size:15px}

/* newsletter */
.news-photo{left:0;top:3210px;width:1200px;height:540px;
  background:radial-gradient(ellipse at 15% 60%,#3a3f45 0%,rgba(30,33,37,0) 45%),
             radial-gradient(ellipse at 90% 55%,#343a40 0%,rgba(30,33,37,0) 40%),
             linear-gradient(180deg,#141618,#1d2024)}
.news-title{top:3388px;font-size:46px}
.news-sub{left:0;top:3454px;width:1200px;text-align:center;font-size:17px;color:var(--silver)}
.news-form{left:180px;top:3516px;width:840px;height:60px;background:var(--white);border-radius:3px;display:flex;align-items:center}
.news-input{flex:1;padding-left:20px;font-size:17px;color:#6b7075}
.news-submit{width:126px;height:48px;margin-right:6px;background:var(--teal);color:var(--white);font-size:17px;
  display:flex;align-items:center;justify-content:center}

/* footer */
.footer-bg{left:0;top:3730px;width:1200px;height:342px;background:var(--bg)}
.footer-brand{left:0;top:3780px;width:1200px;text-align:center;font-family:"Saira Semi Condensed",sans-serif;font-weight:700;font-size:34px;color:var(--white)}
.footer-nav{left:0;top:3868px;width:1200px;display:flex;justify-content:center;gap:38px;list-style:none;font-size:17px;color:var(--white)}
.social{left:0;top:3926px;width:1200px;display:flex;justify-content:center;gap:22px}
.social span{width:40px;height:40px;border-radius:50%;background:#2a2e32;border:2px solid #3c4146;
  display:flex;align-items:center;justify-content:center}
.social span::after{content:"";width:10px;height:10px;border-radius:2px;background:var(--white)}
.social span.on{background:var(--teal);border-color:var(--teal)}
.copyright{left:0;top:4002px;width:1200px;text-align:center;font-size:15px;color:var(--silver)}
</style>
</head>
<body>
<div class="page">

  <!-- Hero -->
  <div class="abs hero-photo" role="img" aria-label="Rider in a VR headset on a roller coaster seat against bright sky"></div>
  <div class="abs brand">Orbit Voltix VR</div>
  <ul class="abs nav"><li>HOME</li><li>EVENTS</li><li>GALLERY</li><li>BLOG</li><li>CONTACTS</li></ul>
  <div class="abs btn-book">BOOK NOW</div>
  <h1 class="abs heading hero-title">Orbit Voltix VR</h1>
  <div class="abs heading hero-sub">Virtual Reality Theme park</div>

  <!-- About -->
  <div class="abs about-bg"></div>
  <div class="abs about-photo" role="img" aria-label="Man in VR headset at a racing simulator wheel"></div>
  <svg class="abs curve" style="top:600px" viewBox="0 0 1200 140" aria-hidden="true">
    <path d="M0 140 L0 80 Q600 20 1200 80 L1200 140 Z" fill="#15171a"/>
    <path d="M120 92 Q600 14 1080 92" fill="none" stroke="var(--teal)" stroke-width="8" stroke-linecap="round"/>
    <path d="M0 80 Q600 20 1200 80" fill="none" stroke="#2d3236" stroke-width="3"/>
  </svg>
  <h2 class="abs heading about-title">About Us</h2>
  <div class="abs about-lead">First and foremost, we are about fun.</div>
  <p class="abs about-text">First we build worlds, then we invite you in. Our park blends free roam arenas, treadmill rigs and simulator rides into one night of pure motion. Every station is tuned by our crew so the move from real floor to virtual sky feels smooth, safe and wild. Bring friends, pick a world and step through the portal with us today.</p>
  <div class="abs btn-outline about-btn">Read More</div>

  <!-- Attractions -->
  <div class="abs rides-bg"></div>
  <svg class="abs curve" style="top:1270px" viewBox="0 0 1200 140" aria-hidden="true">
    <path d="M0 140 L0 80 Q600 20 1200 80 L1200 140 Z" fill="#141619"/>
    <path d="M120 92 Q600 14 1080 92" fill="none" stroke="var(--teal)" stroke-width="8" stroke-linecap="round"/>
  </svg>
  <h2 class="abs heading section-title" style="top:1398px">Attractions &amp; Rides!</h2>

  <div class="abs ride-card" style="left:88px">
    <div class="media" role="img" aria-label="Omnidirectional treadmill pod in a showroom" style="background:linear-gradient(180deg,#8f9aa3,#dfe3e6 55%,#4a5aa8)"></div>
    <div class="ride-label">Trundla(treadmills)</div>
  </div>
  <div class="abs ride-card" style="left:436px">
    <div class="media" role="img" aria-label="Player in headset inside a glowing blue tunnel" style="background:radial-gradient(circle at 50% 40%,#dff4ff 0%,#4aa6e6 30%,#1c2f7a 70%,#0d1438)"></div>
    <div class="ride-label">Stand alone VR stations</div>
  </div>
  <div class="abs ride-card" style="left:784px">
    <div class="media" role="img" aria-label="Riders on a green roller coaster under blue sky" style="background:linear-gradient(180deg,#7fb6e6,#b8d6ef 45%,#3f8a5c 75%,#2c3b4a)"></div>
    <div class="ride-label">VR Simulator rides</div>
  </div>
  <div class="abs dots"><span class="dot"></span><span class="dot on"></span><span class="dot"></span></div>

  <!-- Offer -->
  <div class="abs offer-bg"></div>
  <div class="abs offer-photo" role="img" aria-label="Excited boy wearing a VR headset reaching out"></div>
  <svg class="abs curve" style="top:1950px" viewBox="0 0 1200 140" aria-hidden="true">
    <path d="M0 140 L0 70 Q600 10 1200 70 L1200 140 Z" fill="#15171a"/>
    <path d="M0 70 Q600 10 1200 70" fill="none" stroke="var(--teal)" stroke-width="7"/>
  </svg>
  <h2 class="abs heading offer-title">Buy 2 Tickets</h2>
  <div class="abs heading offer-free">Get 1 FREE</div>
  <p class="abs offer-text">Share the happy with our Buy 2, Get 1 FREE offer when you purchase online by July 13! Tickets valid all summer.</p>
  <div class="abs btn-outline offer-btn">Buy A Ticket</div>

  <!-- Blog -->
  <div class="abs blog-bg"></div>
  <svg class="abs curve" style="top:2570px" viewBox="0 0 1200 140" aria-hidden="true">
    <path d="M0 140 L0 80 Q600 20 1200 80 L1200 140 Z" fill="#1a1c1f"/>
    <path d="M120 92 Q600 14 1080 92" fill="none" stroke="var(--teal)" stroke-width="8" stroke-linecap="round"/>
  </svg>
  <h2 class="abs heading section-title" style="top:2710px">Recent Blog Entries</h2>

  <article class="abs blog-card" style="left:148px;width:412px">
    <div class="media" role="img" aria-label="People trying VR headsets at an event" style="background:linear-gradient(135deg,#6a2f4a,#3b2a55 50%,#1e2a44)"></div>
    <div class="blog-body">
      <div class="blog-title">Quisquam est qui dolorem ipsum quia dolor amet</div>
      <div class="blog-meta">
        <span><svg width="13" height="13" viewBox="0 0 12 12"><circle cx="6" cy="3.5" r="2.5" fill="#fff"/><path d="M1 12a5 5 0 0110 0z" fill="#fff"/></svg>admin</span>
        <span><svg width="13" height="13" viewBox="0 0 12 12"><rect x="1" y="2" width="10" height="9" rx="1" fill="none" stroke="#fff" stroke-width="1.4"/><path d="M1 5h10" stroke="#fff" stroke-width="1.4"/></svg>March 3, 2019</span>
      </div>
      <div class="blog-comments"><svg width="13" height="13" viewBox="0 0 12 12" style="vertical-align:-2px;margin-right:5px"><path d="M1 2h10v6H5l-3 3V8H1z" fill="#fff"/></svg>0 comments</div>
    </div>
  </article>
  <article class="abs blog-card" style="left:640px;width:428px">
    <div class="media" role="img" aria-label="Roller coaster track at a theme park" style="background:linear-gradient(135deg,#3d4a5e,#6b5a4a 50%,#2a3340)"></div>
    <div class="blog-body">
      <div class="blog-title">Neque porro quisquam est qui dolorem</div>
      <div class="blog-meta">
        <span><svg width="13" height="13" viewBox="0 0 12 12"><circle cx="6" cy="3.5" r="2.5" fill="#fff"/><path d="M1 12a5 5 0 0110 0z" fill="#fff"/></svg>admin</span>
        <span><svg width="13" height="13" viewBox="0 0 12 12"><rect x="1" y="2" width="10" height="9" rx="1" fill="none" stroke="#fff" stroke-width="1.4"/><path d="M1 5h10" stroke="#fff" stroke-width="1.4"/></svg>March 3, 2019</span>
      </div>
      <div class="blog-comments"><svg width="13" height="13" viewBox="0 0 12 12" style="vertical-align:-2px;margin-right:5px"><path d="M1 2h10v6H5l-3 3V8H1z" fill="#fff"/></svg>0 comments</div>
    </div>
  </article>

  <!-- Newsletter -->
  <div class="abs news-photo" role="img" aria-label="Dark silhouette of roller coaster loops at dusk"></div>
  <svg class="abs curve" style="top:3150px" viewBox="0 0 1200 140" aria-hidden="true">
    <path d="M0 0 L0 60 Q600 120 1200 60 L1200 0 Z" fill="#121416"/>
    <path d="M120 52 Q600 128 1080 52" fill="none" stroke="var(--teal)" stroke-width="8" stroke-linecap="round"/>
  </svg>
  <h2 class="abs heading section-title news-title">Email Newsletter</h2>
  <p class="abs news-sub">Neque porro quisquam est qui dolorem ipsum quia dolor sit amet, consectetur</p>
  <div class="abs news-form"><span class="news-input">Your email address</span><span class="news-submit">Subscribe</span></div>

  <!-- Footer -->
  <div class="abs footer-bg"></div>
  <svg class="abs curve" style="top:3670px" viewBox="0 0 1200 140" aria-hidden="true">
    <path d="M0 140 L0 80 Q600 20 1200 80 L1200 140 Z" fill="#121416"/>
    <path d="M120 92 Q600 14 1080 92" fill="none" stroke="var(--teal)" stroke-width="8" stroke-linecap="round"/>
  </svg>
  <div class="abs footer-brand">Orbit Voltix VR</div>
  <ul class="abs footer-nav"><li>HOME</li><li>EVENTS</li><li>GALLERY</li><li>BLOG</li><li>CONTACTS</li></ul>
  <div class="abs social" aria-label="Social links"><span></span><span class="on"></span><span></span><span></span></div>
  <div class="abs copyright">Copyright © 2019. All Rights Reserved</div>

</div>
</body>
</html>
```